Irrigation Business needs their business cards modernised and revamped

I would like to keep my current logo, colours and revamp the format of the card.

I would like the card to be clean yet important.

Im not sure if you include texture but i would like the named logo to be indented into the card etc.

show me something alive and free something thats clinical to the point yet has a feel of achievement. i would like people to go nice card.

Target Market(s)

high end clients, corporate, sports field manger, the guys that make the decisions

Industry/Entity Type

Business

Contact Information for Business Card

nformation to be included

Dean Harlow (Director)
0487305526
dean@kolvat.biz
www.kestonfieldworks.com

instagram logo
google logo
facebook logo

Colors

Designer to choose colors to be used in the design.

Requirements
Nice to have
• indentations a really nice feel to the card good texture

```html
<!DOCTYPE html>
<html lang="en">
<head>
<meta charset="utf-8">
<title>Keston Fieldworks – Business Cards</title>
<link rel="stylesheet" href="https://fonts.googleapis.com/css2?family=Open+Sans:wght@400;700;800&display=swap">
<style>
  :root {
    --bg: #2b2b2d;
    --card-white: #f7f7f7;
    --brand-blue: #2f68b4;
    --brand-blue-deep: #2a5ea6;
    --brand-sky: #3aa3dc;
    --ink-white: #ffffff;
    --halo: rgba(255, 255, 255, 0.9);
    --halo-fill: rgba(236, 245, 252, 0.94);
  }
  * { box-sizing: border-box; margin: 0; padding: 0; }
  html, body {
    width: 1200px; height: 840px; overflow: hidden;
    background: var(--bg);
    font-family: "Open Sans", Arial, sans-serif;
  }
  .canvas { position: relative; width: 1200px; height: 840px; }

  .card {
    position: absolute;
    width: 560px; height: 320px;
    border-radius: 4px;
    box-shadow: 0 14px 30px rgba(0,0,0,0.45);
    overflow: hidden;
  }

  /* Front card */
  .card-front {
    left: 80px; top: 90px;
    background: var(--card-white);
    display: flex; flex-direction: column; align-items: center; justify-content: center;
    gap: 14px;
  }
  .brand-mark {
    width: 74px; height: 74px; border-radius: 50%;
    background: var(--brand-sky);
    border: 5px solid var(--brand-blue);
  }
  .brand-name {
    color: var(--brand-blue);
    font-weight: 800;
    font-size: 30px;
    letter-spacing: 0.5px;
    text-transform: uppercase;
    line-height: 1;
  }
  .social-row { display: flex; gap: 8px; margin-top: 4px; }
  .social-dot {
    width: 20px; height: 20px; border-radius: 50%;
    background: var(--brand-blue);
  }

  /* Back card */
  .card-back {
    left: 560px; top: 430px;
    background: linear-gradient(135deg, var(--brand-blue) 0%, var(--brand-blue-deep) 100%);
    color: var(--ink-white);
  }
  .halo {
    position: absolute;
    right: 18px; top: 18px;
    width: 230px; height: 230px; border-radius: 50%;
    background: var(--halo-fill);
    border: 6px solid var(--halo);
    display: flex; flex-direction: column; align-items: center; justify-content: center;
    gap: 10px;
  }
  .halo .brand-mark { width: 48px; height: 48px; border-width: 4px; }
  .halo .brand-name { font-size: 19px; }

  .contact {
    position: absolute;
    left: 36px; bottom: 34px;
    font-size: 14px;
    line-height: 1.35;
  }
  .contact-name { font-weight: 700; font-size: 16px; text-transform: uppercase; }
  .contact-role { text-transform: uppercase; margin-bottom: 8px; font-size: 15px; }
  .contact-line { display: flex; align-items: center; gap: 9px; }
  .contact-line svg { width: 13px; height: 13px; flex: none; fill: var(--ink-white); }
</style>
</head>
<body>
<main class="canvas">

  <section class="card card-front" aria-label="Card front">
    <div class="brand-mark" aria-hidden="true"></div>
    <div class="brand-name">Keston Fieldworks</div>
    <div class="social-row" aria-label="Social profiles">
      <span class="social-dot"></span>
      <span class="social-dot"></span>
      <span class="social-dot"></span>
    </div>
  </section>

  <section class="card card-back" aria-label="Card back">
    <div class="halo">
      <div class="brand-mark" aria-hidden="true"></div>
      <div class="brand-name">Keston Fieldworks</div>
    </div>

    <div class="contact">
      <div class="contact-name">Dean Harlow</div>
      <div class="contact-role">Director</div>
      <div class="contact-line">
        <svg viewBox="0 0 16 16" aria-hidden="true"><path d="M3 1h3l1.5 4-2 1.3a9 9 0 0 0 4.2 4.2L11 8.5l4 1.5v3a2 2 0 0 1-2 2A12 12 0 0 1 1 3a2 2 0 0 1 2-2z"/></svg>
        <span>0487305526</span>
      </div>
      <div class="contact-line">
        <svg viewBox="0 0 16 16" aria-hidden="true"><path d="M1 3h14v10H1z M1.5 3.5 8 9l6.5-5.5" fill="none" stroke="#fff" stroke-width="1.6"/></svg>
        <span>dean@kolvat.biz</span>
      </div>
      <div class="contact-line">
        <svg viewBox="0 0 16 16" aria-hidden="true"><circle cx="8" cy="8" r="6.5" fill="none" stroke="#fff" stroke-width="1.5"/><path d="M1.5 8h13M8 1.5c-3 3.5-3 9.5 0 13M8 1.5c3 3.5 3 9.5 0 13" fill="none" stroke="#fff" stroke-width="1.2"/></svg>
        <span>www.kestonfieldworks.com</span>
      </div>
    </div>
  </section>

</main>
</body>
</html>
```